New Interrior Decoration company needs new website

We need a website for our new company specialising in interior decoration to residential and commercial markets.
We supply and install decorative and printed films for office and home decoration such as feature walls.
We would like to keep the design simple and clean.

Target Market(s)

Architects and interior designaers

Industry/Entity Type

It Company

Number of Pages Required

5+ page

Font styles to use
Sans Serif

Requirements
Must have
• Home page,
• Services/products page (split into commercial and residential)
• Gallery (split into commercial and residential)
• contact form and page
Nice to have
• Very clean and minimalistic design.

```html
<!DOCTYPE html>
<html lang="en">
<head>
<meta charset="utf-8">
<title>Lumen Interiors</title>
<link rel="stylesheet" href="https://fonts.googleapis.com/css2?family=Lato:ital,wght@0,400;0,700;0,900;1,900&family=Arimo:wght@400;700&display=swap">
<style>
:root{
  --blue:#0a5cbf;
  --ink:#444;
  --ink-dark:#1d1d1d;
  --muted:#8a8a8a;
  --band:#f2f2f2;
  --rule:#d4d4d4;
  --white:#fff;
}
*{box-sizing:border-box;margin:0;padding:0}
html,body{width:1200px;height:2365px;overflow:hidden;background:var(--white)}
body{position:relative;font-family:"Arimo",Arial,sans-serif;color:var(--ink)}
.abs{position:absolute}

/* header */
.site-header{left:0;top:0;width:1200px;height:110px;background:var(--white)}
.brand{left:77px;top:28px;display:flex;align-items:center;gap:14px}
.brand-mark{width:56px;height:56px;background:var(--blue)}
.brand-name{font-family:"Lato",sans-serif;font-weight:900;font-size:34px;line-height:30px;color:#2c2c2c;letter-spacing:.5px}
.main-nav{left:532px;top:47px;display:flex;gap:0}
.main-nav a{font-size:17px;color:#333;text-decoration:none;letter-spacing:.3px}
.main-nav a.active{color:var(--blue)}

/* hero */
.hero{left:0;top:110px;width:1200px;height:573px;background:linear-gradient(180deg,#4a4c4b 0%,#3c3e3d 55%,#6d706f 78%,#d9dcdc 84%,#f0f1f1 100%)}
.hero-title{left:0;top:125px;width:1200px;text-align:center;font-family:"Lato",sans-serif;font-style:italic;font-weight:900;font-size:44px;line-height:52px;color:var(--white);text-shadow:0 2px 6px rgba(0,0,0,.6)}
.hero-call{left:0;top:262px;width:1200px;display:flex;justify-content:center;align-items:center;gap:26px;font-family:"Lato",sans-serif;font-weight:700;font-size:38px;color:var(--ink-dark)}
.call-icon{width:70px;height:70px}

/* welcome */
.welcome-title{left:0;top:738px;width:1200px;text-align:center;font-family:"Lato",sans-serif;font-size:42px;color:var(--ink)}
.welcome-text{left:140px;top:804px;width:920px;text-align:center;font-size:14.5px;line-height:27px;color:var(--muted)}
.design-card h3{font-family:"Lato",sans-serif;font-weight:400;font-size:20px;color:#222;margin-bottom:10px}
.design-card p{font-size:14.5px;line-height:25px;color:var(--muted)}
.design-card a{display:inline-block;margin-top:10px;font-size:15px;color:var(--blue);text-decoration:none}
.card-commercial{left:96px;top:912px;width:230px;text-align:right}
.card-residential{left:872px;top:910px;width:235px;text-align:left}
.photo{display:block}
.photo-commercial{left:342px;top:911px;width:249px;height:167px;background:linear-gradient(135deg,#d9d6cf,#a89a83 55%,#4a3f33)}
.photo-residential{left:607px;top:911px;width:250px;height:167px;background:linear-gradient(135deg,#e6ef9a,#bcd24a 50%,#e9ece6)}

/* testimonial */
.testimonial{left:0;top:1140px;width:1200px;height:303px;background:var(--band);border-top:1px solid var(--rule);border-bottom:1px solid var(--rule)}
.testimonial h2{position:absolute;left:0;top:44px;width:1200px;text-align:center;font-family:"Lato",sans-serif;font-weight:400;font-size:42px;color:var(--ink)}
.testimonial blockquote{position:absolute;left:210px;top:118px;width:780px;text-align:center;font-size:14.5px;line-height:27px;color:#555}
.testimonial .client{position:absolute;left:0;top:218px;width:1200px;text-align:center;font-family:"Lato",sans-serif;font-size:16px;color:#666}
.client b{color:var(--blue);font-weight:700}
.client small{font-size:13px;color:#999}
.quote-mark{position:absolute;font-family:"Lato",sans-serif;font-weight:900;font-size:150px;line-height:1;color:#d6d6d6}
.quote-open{left:135px;top:48px}
.quote-close{left:995px;top:155px}

/* gallery */
.gallery-title{left:0;top:1500px;width:1200px;text-align:center;font-family:"Lato",sans-serif;font-size:42px;color:var(--ink)}
.tile{width:333px;height:208px}
.tile-feature{background:var(--blue);display:flex;flex-direction:column;align-items:center;justify-content:center;color:var(--white)}
.tile-feature strong{font-size:21px;font-weight:400;letter-spacing:.3px}
.tile-feature span{font-size:16px;margin-top:8px}
.btn-view{left:506px;top:2048px;width:188px;height:62px;background:var(--blue);border-radius:4px;color:var(--white);font-family:"Lato",sans-serif;font-size:20px;display:flex;align-items:center;justify-content:center;text-decoration:none}

/* footer */
.site-footer{left:0;top:2172px;width:1200px;height:193px;background:var(--band)}
.footer-nav{position:absolute;left:77px;top:25px;display:flex;align-items:center}
.footer-nav a{font-size:16px;color:#444;text-decoration:none;margin-right:36px}
.footer-nav a.active{border:1px solid var(--blue);color:var(--blue);padding:10px 18px;margin-right:24px}
.social{position:absolute;top:23px;width:47px;height:47px;border-radius:50%;border:1.5px solid #777}
.social.filled{background:var(--blue);border-color:var(--blue)}
.footer-rule{position:absolute;left:77px;top:91px;width:1046px;height:1px;background:var(--rule)}
.contact-item{position:absolute;top:114px;display:flex;align-items:center;gap:22px;font-size:14px;line-height:20px;color:#555}
.contact-item svg{flex:none}
.copyright b{color:var(--blue);font-weight:400}
</style>
</head>
<body>

<header class="site-header abs">
  <div class="brand abs">
    <span class="brand-mark"></span>
    <span class="brand-name">LUMEN<br>INTERIORS</span>
  </div>
  <nav class="main-nav abs">
    <a class="active" href="#" style="margin-right:58px">HOME</a>
    <a href="#" style="margin-right:44px">ABOUT US</a>
    <a href="#" style="margin-right:66px">SERVICES</a>
    <a href="#" style="margin-right:47px">GALLERY</a>
    <a href="#">CONTACT</a>
  </nav>
</header>

<section class="hero abs" role="img" aria-label="Photo of a white sofa with cushions against a dark textured feature wall"></section>
<h1 class="hero-title abs">WE ARE SPECIALISING IN INTERIOR DECORATION FOR<br>RESIDENTIAL &amp; COMMERCIAL MARKETS.</h1>
<div class="hero-call abs">
  <span>CALL US KNOW</span>
  <svg class="call-icon" viewBox="0 0 70 70" aria-hidden="true">
    <circle cx="35" cy="35" r="33" fill="none" stroke="#1d1d1d" stroke-width="2.5"/>
    <path d="M25 22c2-2 4-2 5 0l3 5c1 2 0 3-1 4l-2 2c2 4 5 7 9 9l2-2c1-1 2-2 4-1l5 3c2 1 2 3 0 5l-3 3c-3 2-10-1-16-7s-9-13-7-16z" fill="#1d1d1d"/>
    <path d="M38 22a10 10 0 0 1 10 10M38 16a16 16 0 0 1 16 16" fill="none" stroke="#1d1d1d" stroke-width="2.5"/>
  </svg>
  <span>+1 555 014 2789</span>
</div>

<h2 class="welcome-title abs">Welcome To Lumen Interiors</h2>
<p class="welcome-text abs">Lorem Ipsum is simply dummy text of the printing and typesetting industry. Lorem Ipsum has been the industry's standard dummy text ever since the 1500s, when an unknown printer took a galley of type and scrambled it to make a type specimen book. It has survived not only five centuries, but also the leap into electronic typesetting,</p>

<article class="design-card card-commercial abs">
  <h3>COMMERCIAL DESIGN</h3>
  <p>Lorem Ipsum is simply dummy text of the printing and typesetting industry. Lorem Ipsum has been the industry's standard..</p>
  <a href="#">READ MORE... &#187;</a>
</article>
<div class="photo photo-commercial abs" role="img" aria-label="Photo of a modern commercial interior with a curved wooden reception counter"></div>
<div class="photo photo-residential abs" role="img" aria-label="Photo of a living room with a bright lime patterned feature wall"></div>
<article class="design-card card-residential abs">
  <h3>RESIDENTIAL DESIGN</h3>
  <p>Lorem Ipsum is simply dummy text of the printing and typesetting industry. Lorem Ipsum has been the industry's standard..</p>
  <a href="#">READ MORE... &#187;</a>
</article>

<section class="testimonial abs">
  <span class="quote-mark quote-open">&#8220;</span>
  <h2>Happy Client</h2>
  <blockquote>" Lorem Ipsum is simply dummy text of the printing and typesetting industry. Lorem Ipsum has been the industry's standard dummy text ever since the 1500s, when an unknown printer took a galley of type and scrambled it to make a type specimen book. It has survived "</blockquote>
  <p class="client"><b>CLIENT NAME</b> - <small>clientsite.example</small></p>
  <span class="quote-mark quote-close">&#8221;</span>
</section>

<h2 class="gallery-title abs">Our Gallery</h2>
<div class="tile tile-feature abs" style="left:77px;top:1588px" role="img" aria-label="Residential dream house interior under a blue overlay">
  <strong>DREAM HOUSE</strong><span>Residential</span>
</div>
<div class="tile abs" style="left:434px;top:1588px;background:linear-gradient(135deg,#5a2414,#9a3e1e 50%,#2a1a18)" role="img" aria-label="Photo of a lilac lounge chair beside a bookshelf and lamp"></div>
<div class="tile abs" style="left:790px;top:1588px;background:linear-gradient(135deg,#d8d8d4,#c9c6c0 55%,#a58a78)" role="img" aria-label="Photo of an office corridor wall with printed circles"></div>
<div class="tile abs" style="left:77px;top:1818px;background:linear-gradient(180deg,#5a2a35,#7a4248 55%,#c9b9a0)" role="img" aria-label="Photo of a cream sectional sofa against a plum wall"></div>
<div class="tile abs" style="left:434px;top:1818px;background:linear-gradient(135deg,#5d5f5e,#cfd0cc 50%,#4b4c4a)" role="img" aria-label="Photo of a grey kitchen with pendant lamps and tall windows"></div>
<div class="tile abs" style="left:790px;top:1818px;background:linear-gradient(135deg,#e7e3d6,#c9a457 45%,#c9362a)" role="img" aria-label="Photo of a room with a multicoloured wood plank wall and red armchair"></div>
<a class="btn-view abs" href="#">VIEW ALL</a>

<footer class="site-footer abs">
  <nav class="footer-nav">
    <a class="active" href="#">Home</a>
    <a href="#">About Us</a>
    <a href="#">Services</a>
    <a href="#">Gallery</a>
    <a href="#">Contact</a>
  </nav>
  <span class="social filled" style="left:955px" aria-label="Social profile"></span>
  <span class="social" style="left:1015px" aria-label="Social profile"></span>
  <span class="social" style="left:1074px" aria-label="Social profile"></span>
  <div class="footer-rule"></div>

  <div class="contact-item" style="left:77px">
    <svg width="52" height="52" viewBox="0 0 52 52" aria-hidden="true"><circle cx="26" cy="26" r="26" fill="#0a5cbf"/><path d="M26 14a8 8 0 0 0-8 8c0 6 8 15 8 15s8-9 8-15a8 8 0 0 0-8-8zm0 11a3 3 0 1 1 0-6 3 3 0 0 1 0 6z" fill="#fff"/></svg>
    <span>Lorem ipsum is simple text<br>of type setting industry..</span>
  </div>
  <div class="contact-item" style="left:354px">
    <svg width="52" height="52" viewBox="0 0 52 52" aria-hidden="true"><circle cx="26" cy="26" r="25" fill="none" stroke="#777" stroke-width="1.5"/><path d="M19 17c1.5-1.5 3-1.5 4 0l2 3.5c.7 1.4 0 2.2-.8 3l-1.4 1.4c1.4 3 3.6 5.2 6.6 6.6l1.4-1.4c.8-.8 1.6-1.5 3-.8l3.5 2c1.5 1 1.5 2.5 0 4l-2 2c-2.3 1.5-7.5-.8-11.7-5s-6.5-9.4-5-11.7z" fill="#555"/></svg>
    <span>555 014 7890</span>
  </div>
  <div class="contact-item" style="left:592px">
    <svg width="52" height="52" viewBox="0 0 52 52" aria-hidden="true"><circle cx="26" cy="26" r="25" fill="none" stroke="#777" stroke-width="1.5"/><rect x="17" y="20" width="18" height="13" rx="1.5" fill="#555"/><path d="M17 21l9 7 9-7" fill="none" stroke="#fff" stroke-width="1.5"/></svg>
    <span style="margin-left:-8px">info@lumeninteriors.example</span>
  </div>
  <p class="contact-item copyright" style="left:878px;top:126px">&#169;<b>LumenInteriors</b>- 2016. All<br>rights reserved.</p>
</footer>

</body>
</html>
```